Wellpath Ledgers New Website

Please review the attached Design Brief with additional details. Thank you!

The goal is to create a website that effectively communicates the benefits of WellPath Ledgers to eye care professionals. The website should streamline the process of understanding and utilizing WellPath Ledgers' services, emphasizing improved patient outcomes, increased referrals, and enhanced patient engagement.

Target Market(s)

Eyecare Professionals

Number of Pages Required

4 page

```html
<!DOCTYPE html>
<html lang="en">
<head>
<meta charset="utf-8">
<title>Wellpath Ledgers – Contact</title>
<link href="https://fonts.googleapis.com/css2?family=Open+Sans:wght@400;600;700&display=swap" rel="stylesheet">
<style>
:root{
  --navy:#0d5076;
  --panel:#06235f;
  --icon:#0b2a66;
  --orange:#f7a23f;
  --footer:#181222;
  --field:#f4f4f4;
  --muted:#9a9a9a;
  --white:#fff;
}
*{margin:0;padding:0;box-sizing:border-box}
html,body{width:707px;height:1200px;overflow:hidden}
body{position:relative;background:var(--white);font-family:"Open Sans",sans-serif;color:var(--navy)}
.abs{position:absolute}
.hero{left:0;top:0;width:707px;height:205px;background:linear-gradient(100deg,#2d4a78 0%,#3f5f8f 45%,#2a4775 100%)}
.hero-bar{left:0;top:205px;width:707px;height:2.5px;background:var(--orange)}
.topline{top:12px;font-size:6px;color:#fff;font-weight:600;white-space:nowrap}
.quote-btn{left:498px;top:11px;width:66px;height:9px;border-bottom:3px solid #3a8a6a;font-size:5.5px;color:#fff;text-align:center}
.brand-shape{left:0;top:13px;width:260px;height:41px}
.nav{left:0;top:27px;width:707px;height:27px;background:#fff}
.brand{left:46px;top:21px;font-size:13px;font-weight:700;color:#1c3fa8;display:flex;align-items:center;gap:5px}
.brand i{width:10px;height:10px;background:var(--orange);display:block}
.menu{top:36px;font-size:7px;color:#5a6b7a}
.menu.active{color:var(--navy);font-weight:700}
.hero-kicker{left:63px;top:110px;font-size:12px;color:#fff}
.hero-title{left:63px;top:126px;font-size:30px;font-weight:700;color:#fff;white-space:nowrap}
.eyebrow{font-size:7px;color:var(--orange)}
.h2{font-size:21px;font-weight:700;color:var(--navy);line-height:1.35}
.card{top:311px;height:57px;border:1px solid #e5e7ee;box-shadow:0 1px 3px rgba(0,0,0,.06);background:#fff}
.card .ico{position:absolute;left:12px;top:13px;width:30px;height:30px;background:var(--icon);border-radius:2px;display:flex;align-items:center;justify-content:center}
.card .txt{position:absolute;left:51px;top:14px;font-size:7.5px;font-weight:600;color:var(--navy);line-height:14px;white-space:nowrap}
.card .phone{font-size:13px;color:var(--orange);font-weight:400}
.panel{left:46px;top:454px;width:251px;height:319px;background:var(--panel);border-radius:2px}
.panel-copy{left:63px;top:561px;width:220px;font-size:8.4px;line-height:14.8px;color:#fff}
.map{left:63px;top:627px;width:219px;height:117px;background:linear-gradient(135deg,#efe6cf,#e4d9bd 60%,#cfe0e8)}
.map-tag{left:68px;top:632px;width:126px;height:28px;background:#fff;padding:4px 8px}
.map-tag b{display:block;font-size:8px;font-weight:600;color:var(--navy)}
.map-tag span{font-size:6px;color:#444}
.field{background:var(--field);border-radius:2px;font-size:7px;color:var(--muted);padding:10px 8px 0}
.send{left:319px;top:733px;width:64px;height:22px;background:var(--orange);color:#fff;font-size:7px;font-weight:700;display:flex;align-items:center;justify-content:center}
.footer-bg{left:0;top:860px;width:707px;height:340px}
.f-brand{left:70px;top:945px;font-size:18px;font-weight:700;color:#1c3fa8;display:flex;align-items:center;gap:6px}
.f-brand i{width:12px;height:12px;background:var(--orange);border-radius:50%;display:block}
.f-text{font-size:7.2px;line-height:12.4px;color:#c9c6d2}
.f-head{font-size:9px;font-weight:700;color:#fff}
.f-link{font-size:7.4px;color:#c9c6d2}
.soc{top:1031px;width:19px;height:19px;border-radius:3px;background:#2a2140}
.soc.on{background:var(--orange)}
.news-in{left:487px;top:1007px;width:114px;height:27px;background:#fff;font-size:7px;color:#666;padding:9px 14px}
.news-btn{left:601px;top:1007px;width:29px;height:27px;background:var(--orange)}
.dot{width:28px;height:28px;border-radius:50%;background:#2a2140;display:flex;align-items:center;justify-content:center}
.dot.on{background:var(--orange)}
.c-title{font-size:9px;font-weight:700;color:#fff}
.c-sub{font-size:7.4px;color:#c9c6d2;white-space:nowrap}
.rule{left:74px;top:1165px;width:559px;height:1px;background:#3a3247}
.copy{left:0;top:1177px;width:707px;text-align:center;font-size:7.5px;color:#fff}
</style>
</head>
<body>
<div class="abs hero" role="img" aria-label="Photo of team members working at computers in a blue-toned office"></div>
<div class="abs hero-bar"></div>

<span class="abs topline" style="left:276px">&#9679; 48 Linden Row, Country, 000002</span>
<span class="abs topline" style="left:416px">Follow Us:</span>
<svg class="abs" style="left:451px;top:14px" width="26" height="5"><circle cx="2.5" cy="2.5" r="2" fill="#fff"/><circle cx="11" cy="2.5" r="2" fill="#fff"/><circle cx="19.5" cy="2.5" r="2" fill="#fff"/></svg>
<div class="abs quote-btn">GET QUOTATION</div>

<div class="abs nav"></div>
<svg class="abs brand-shape" viewBox="0 0 260 41"><path d="M0 0H230C245 0 250 14 260 14V41H0Z" fill="#fff"/></svg>
<div class="abs brand"><i></i>Wellpath Ledgers</div>
<span class="abs menu active" style="left:264px;font-weight:400">Home</span>
<span class="abs menu" style="left:319px">About Us</span>
<span class="abs menu" style="left:371px">Conditions</span>
<span class="abs menu active" style="left:426px">Services</span>
<span class="abs menu" style="left:489px">Gallery</span>
<span class="abs menu" style="left:537px">Team</span>
<span class="abs menu" style="left:585px">Contact Us</span>

<div class="abs hero-kicker">CONTACT</div>
<div class="abs hero-title">Get in touch with us</div>

<div class="abs eyebrow" style="left:0;width:707px;text-align:center;top:244px">Let Us Know How We Can Be Of Assistance</div>
<div class="abs h2" style="left:0;width:712px;text-align:center;top:257px">Drop us a line and let’s talk</div>

<div class="abs card" style="left:48px;width:194px">
  <div class="ico"><svg width="16" height="16" viewBox="0 0 24 24" fill="none" stroke="#fff" stroke-width="1.4"><path d="M5 3h4l2 5-2.5 1.5a11 11 0 0 0 6 6L16 13l5 2v4a2 2 0 0 1-2 2A17 17 0 0 1 3 5a2 2 0 0 1 2-2z"/></svg></div>
  <div class="txt">Phone Number<br><span class="phone">+014 (552) 3170</span></div>
</div>
<div class="abs card" style="left:261px;width:194px">
  <div class="ico"><svg width="16" height="16" viewBox="0 0 24 24" fill="none" stroke="#fff" stroke-width="1.4"><path d="M3 10v11h18V10"/><path d="M3 21l7-6m11 6l-7-6M3 10l9 6 9-6"/><circle cx="12" cy="7" r="3"/></svg></div>
  <div class="txt" style="top:15px">Any Questions? Email us<br>Support@wellpathledgers.com</div>
</div>
<div class="abs card" style="left:473px;width:194px">
  <div class="ico"><svg width="16" height="16" viewBox="0 0 24 24" fill="none" stroke="#fff" stroke-width="1.4"><path d="M12 15s-5-5-5-8.5a5 5 0 0 1 10 0C17 10 12 15 12 15z"/><circle cx="12" cy="7" r="1.8"/><path d="M7 14l-4 7h18l-4-7"/></svg></div>
  <div class="txt" style="top:16px">8420 Meridian Avenue<br>State, USA</div>
</div>

<div class="abs panel"></div>
<div class="abs eyebrow" style="left:63px;top:481px;font-size:8px">Need Some Advice?</div>
<div class="abs h2" style="left:62px;top:496px;color:#fff;line-height:28px;width:230px">Feel free to contact us</div>
<p class="abs panel-copy">Lorem ipsum dolor sit amet, consectetur adipiscing elit, sed do eiusmod tempor incididunt ut labore et dolore magna aliqua. Ut enim ad minim</p>
<div class="abs map" role="img" aria-label="Map showing the regional office location"></div>
<div class="abs map-tag"><b>Wellpath Ledgers offices</b><span>View larger map</span></div>
<div class="abs" style="left:255px;top:689px;width:20px;height:44px;background:#fff;box-shadow:0 1px 2px rgba(0,0,0,.2)"></div>
<svg class="abs" style="left:255px;top:689px" width="20" height="44"><path d="M10 6v9M5.5 10.5h9M5.5 32.5h9" stroke="#555" stroke-width="2"/></svg>

<div class="abs eyebrow" style="left:319px;top:460px;font-size:8px">Need Some Advice?</div>
<div class="abs h2" style="left:317px;top:474px">Contact Us To Learn More.</div>
<div class="abs field" style="left:318px;top:521px;width:167px;height:27px">First Name</div>
<div class="abs field" style="left:502px;top:521px;width:167px;height:27px">Last Name</div>
<div class="abs field" style="left:318px;top:560px;width:167px;height:26px">Email Address</div>
<div class="abs field" style="left:502px;top:560px;width:167px;height:26px">Phone</div>
<div class="abs field" style="left:318px;top:600px;width:351px;height:26px">Subject</div>
<div class="abs field" style="left:318px;top:640px;width:352px;height:67px">Message goes here</div>
<div class="abs send">Send Mesage</div>

<svg class="abs footer-bg" viewBox="0 0 707 340" preserveAspectRatio="none">
  <path d="M0 30C60 5 160 0 230 10S400 50 560 50C620 50 680 45 707 38V340H0Z" fill="var(--orange)"/>
  <path d="M0 52C60 25 160 20 230 28S400 66 560 66C620 66 680 48 707 40V340H0Z" fill="var(--footer)"/>
</svg>

<div class="abs f-brand"><i></i>Wellpath Ledgers</div>
<p class="abs f-text" style="left:74px;top:990px;width:185px">Lorem ipsum dolor sit amet, consectetur adipiscing elit, sed do eiusmod tempor incididunt ut</p>
<div class="abs soc on" style="left:74px"></div>
<div class="abs soc" style="left:97px"></div>
<div class="abs soc" style="left:119px"></div>
<div class="abs soc" style="left:141px"></div>

<div class="abs f-head" style="left:289px;top:947px">Quick Links</div>
<span class="abs f-link" style="left:289px;top:975px">Home</span>
<span class="abs f-link" style="left:289px;top:990px">Services</span>
<span class="abs f-link" style="left:289px;top:1005px">About Us</span>
<span class="abs f-link" style="left:289px;top:1020px">Contact</span>
<span class="abs f-link" style="left:289px;top:1035px">Blog</span>
<span class="abs f-link" style="left:289px;top:1051px">Testimonials</span>
<span class="abs f-link" style="left:368px;top:975px">Cookies Policy</span>
<span class="abs f-link" style="left:368px;top:990px">Terms of Use</span>
<span class="abs f-link" style="left:368px;top:1005px">Careers</span>
<span class="abs f-link" style="left:368px;top:1020px">Our Team</span>
<span class="abs f-link" style="left:368px;top:1035px">More</span>

<div class="abs f-head" style="left:487px;top:947px">Newsletters</div>
<p class="abs f-text" style="left:487px;top:972px;width:150px">Lorem ipsum dolor sit amet, consectetur adi piscing elit, sed do eiusmod tempor</p>
<div class="abs news-in">Enter Email Address</div>
<div class="abs news-btn"><svg width="29" height="27"><path d="M12 8l6 5.5-6 5.5" fill="none" stroke="#fff" stroke-width="2"/></svg></div>

<div class="abs dot" style="left:74px;top:1098px"><svg width="10" height="12" viewBox="0 0 10 12"><path d="M5 12S0 7 0 4.5a5 5 0 0 1 10 0C10 7 5 12 5 12z" fill="#7a6e92"/><circle cx="5" cy="4.5" r="1.6" fill="#2a2140"/></svg></div>
<div class="abs c-title" style="left:112px;top:1098px">Address</div>
<div class="abs c-sub" style="left:112px;top:1113px">76 Harbor Lane</div>

<div class="abs dot on" style="left:215px;top:1098px"><svg width="13" height="9" viewBox="0 0 13 9"><rect x=".5" y=".5" width="12" height="8" fill="none" stroke="#fff"/><path d="M.5.5l6 4.5 6-4.5" fill="none" stroke="#fff"/></svg></div>
<div class="abs c-title" style="left:253px;top:1098px">Email Us</div>
<div class="abs c-sub" style="left:253px;top:1113px">supportinfo@wellpathmail.com</div>

<div class="abs dot" style="left:372px;top:1098px"><svg width="12" height="12" viewBox="0 0 24 24"><path d="M5 3h4l2 5-2.5 1.5a11 11 0 0 0 6 6L16 13l5 2v4a2 2 0 0 1-2 2A17 17 0 0 1 3 5a2 2 0 0 1 2-2z" fill="#7a6e92"/></svg></div>
<div class="abs c-title" style="left:410px;top:1098px">Contact Us</div>
<div class="abs c-sub" style="left:410px;top:1113px">+014(5523) 170 42</div>

<div class="abs dot" style="left:507px;top:1098px"><svg width="13" height="13" viewBox="0 0 13 13"><circle cx="6.5" cy="6.5" r="5.5" fill="none" stroke="#7a6e92" stroke-width="1.2"/><path d="M6.5 3.5v3h2.5" fill="none" stroke="#7a6e92" stroke-width="1.2"/></svg></div>
<div class="abs c-title" style="left:544px;top:1098px">Opening Hour</div>
<div class="abs c-sub" style="left:544px;top:1113px">Mon - Friday 10 am - 8pm</div>

<div class="abs rule"></div>
<div class="abs copy">WELLPATH LEDGERS</div>
</body>
</html>
```